Create website for home automation - Control your lighting, fans, blinds etc remotely by smartphone

Plan for SHOPIFY Website - Our Clever Dwelling
Company name: Our Clever Dwelling
Company Slogan: Calm Evenings Come Naturally
Clean, Modern, Easy to Navigate, easy to maintain - not a lot of coding. We need flash technology but displaying simply what we do.
What we provide:
We will be offering wireless switch which can be added to iOS/Android App via WiFi, allowing users to remotely turn on/off connected lights, fans, security cameras, appliances, irrigation, humidifier separately from anywhere at any time.
Control your home away from home. No more wandering of your mind on those lights or appliances which you might have left switched on. No need to drive back home to check and switch them off. Save that energy, money and time just with a click of your phone no matter how far you are from home.
Replace your home electrical switches with smart switches. They retrofit existing electrical switches and allow you to make the transformation as needed.
Easy to use and intuitive app allows you to control your lights and devices just at a click. Set any kind of ambiance suiting your occasion.
Set scenes in smartphone app to group and operate your devices just at a button click. Same device can be included in more than one scene.
Collections and Products
Light Switches
Wall Plugs
Fan Switch
Pendants etc special lighting types.
Light Dimmers
Blind Controllers
Home Page:
Home page needs to telling customers what we do and how we do it in a few words to grab people.
Phone
Email
Support – Download instructions per product
Client login
Wholesale login
Promotional video to be on home screen - this is a short 1.5 - 2 min illustration introduction video to who we are and what we do - this is yet to be created)
Social media link - Friendwall
Pages:
FAQ
About Us
Support/Shipping/Returns policy
Support/Installation
Blog posts
Product pages:
Description
Price
Space for where a video will be featured - how each product works/installation.
Reviews
Our competition:
http://www.brivo.com.au
https://lumigardenhub.com.au/2018/04/05/best-smart-light-switches-and-plugs/
https://www.tavelinq.com

```html
<!DOCTYPE html>
<html lang="en">
<head>
<meta charset="utf-8">
<title>Our Clever Dwelling — Home</title>
<link rel="stylesheet" href="https://fonts.googleapis.com/css2?family=Roboto:wght@400;500;700;900&family=Open+Sans:wght@400;600;700&display=swap">
<style>
:root{
  --navy:#132a78;
  --blue:#1d5db5;
  --band:#1b3f8c;
  --ink:#333;
  --muted:#666;
  --grey-bg:#f2f2f2;
  --white:#fff;
  --footer:#141414;
  --footer-text:#cfcfcf;
}
*{margin:0;padding:0;box-sizing:border-box}
html,body{width:1200px;height:4700px;overflow:hidden}
body{position:relative;background:var(--white);font-family:'Open Sans',sans-serif;color:var(--ink)}
.abs{position:absolute}

/* hero */
.hero{left:0;top:0;width:1200px;height:630px;background:radial-gradient(ellipse at 75% 30%,#c98a4a 0%,#7a4a26 35%,#3a2417 70%,#1d120c 100%)}
.topbar{top:22px;right:100px;display:flex;gap:22px;font-size:13px;color:var(--white)}
.topbar span{display:flex;align-items:center;gap:6px}
.topbar span+span::before{content:"|";margin-right:16px;opacity:.7}
.brand{left:110px;top:40px;display:flex;align-items:center;gap:12px}
.brand-mark{width:46px;height:46px;border:3px solid var(--white);border-radius:50%}
.brand-name{font-family:'Roboto',sans-serif;font-weight:700;font-size:22px;color:var(--white);line-height:1.1}
.brand-slogan{font-family:'Roboto',sans-serif;font-weight:700;font-size:11px;color:var(--white);letter-spacing:1px}
.nav{top:82px;left:398px;display:flex;gap:22px;font-family:'Roboto',sans-serif;font-weight:700;font-size:15px;color:var(--white)}
.nav-btn{top:70px;width:44px;height:44px;border-radius:50%;display:flex;align-items:center;justify-content:center}
.nav-search{left:988px;border:2px solid var(--white)}
.nav-cart{left:1044px;background:var(--white)}
.hero-title{top:180px;left:0;width:1200px;text-align:center;font-family:'Roboto',sans-serif;font-weight:700;font-size:50px;color:var(--white)}
.hero-btn{top:260px;left:500px;width:200px;height:60px;border:2px solid var(--white);border-radius:30px;display:flex;align-items:center;justify-content:center;color:var(--white);font-family:'Roboto',sans-serif;font-weight:700;font-size:15px}
.hero-photo{top:345px;left:390px;width:420px;height:285px;background:linear-gradient(160deg,#2f3440,#0e1016 60%,#c19a7c);border-radius:18px 18px 0 0}

/* section titles */
.section-title{left:0;width:1200px;text-align:center;font-family:'Roboto',sans-serif;font-weight:700;font-size:42px;color:var(--navy)}

/* welcome */
.welcome-text{top:790px;left:220px;width:760px;text-align:center;font-size:13.5px;line-height:26px;color:var(--muted)}
.video{top:915px;left:413px;width:374px;height:250px;background:linear-gradient(135deg,#9aa0a6,#4d5259 60%,#2d3035);box-shadow:0 2px 8px rgba(0,0,0,.25)}
.play{top:1012px;left:572px}

/* collections */
.collections{top:1265px;left:0;width:1200px;height:1540px;background:var(--grey-bg)}
.tile{background:var(--white);display:flex;align-items:center;justify-content:center}
.tile-fill{border-radius:8px}
.label{text-align:center;font-size:22px;color:#444}

/* newsletter */
.newsletter{top:2805px;left:0;width:1200px;height:388px;background:var(--band)}
.news-title{top:2890px;left:0;width:1200px;text-align:center;font-family:'Roboto',sans-serif;font-weight:700;font-size:42px;color:var(--white)}
.news-sub{top:2965px;left:0;width:1200px;text-align:center;font-size:17px;color:var(--white)}
.news-input{top:3030px;left:300px;width:455px;height:60px;background:var(--white);padding-left:28px;display:flex;align-items:center;font-size:14px;color:#777}
.news-btn{top:3030px;left:755px;width:145px;height:60px;background:var(--blue);color:var(--white);display:flex;align-items:center;justify-content:center;font-family:'Roboto',sans-serif;font-weight:700;font-size:15px}

/* features */
.feature-title{font-family:'Roboto',sans-serif;font-weight:700;font-size:40px;color:var(--navy)}
.feature-text{width:380px;font-size:13.5px;line-height:26px;color:var(--muted)}
.pill{width:134px;height:48px;border-radius:24px;background:var(--blue);color:var(--white);display:flex;align-items:center;justify-content:center;font-family:'Roboto',sans-serif;font-weight:700;font-size:13px}

/* footer */
.footer{top:4300px;left:0;width:1200px;height:400px;background:var(--footer)}
.foot-head{top:4368px;font-family:'Roboto',sans-serif;font-weight:700;font-size:17px;color:var(--white)}
.foot-list{top:4410px;list-style:none;font-size:12.5px;line-height:27px;color:var(--footer-text)}
.social{top:4405px;left:528px;list-style:none;font-size:12.5px;color:var(--footer-text)}
.social li{display:flex;align-items:center;gap:14px;height:44px}
.social i{width:30px;height:30px;border-radius:50%;background:#2e2e2e;border:1px solid #555}
.foot-about{top:4410px;left:767px;width:330px;font-size:12.5px;line-height:25px;color:var(--footer-text)}
.foot-rule{top:4615px;left:100px;width:1000px;height:1px;background:#333}
.copyright{top:4645px;left:100px;font-size:12.5px;color:var(--footer-text)}
.cards{top:4638px;left:868px;display:flex;gap:6px}
.cards i{width:46px;height:26px;border-radius:3px;background:#8f8f8f}
</style>
</head>
<body>

<header>
  <div class="abs hero" role="img" aria-label="Warm living room scene with hands holding a home control tablet"></div>
  <div class="abs topbar">
    <span>☎ 1 800 555 0142</span>
    <span>✉ hello@ourcleverdwelling.example</span>
    <span>Support</span>
    <span>Client login</span>
    <span>Wholesale login</span>
  </div>
  <div class="abs brand">
    <div class="brand-mark"></div>
    <div>
      <div class="brand-name">OUR CLEVER DWELLING</div>
      <div class="brand-slogan">Calm Evenings Come Naturally</div>
    </div>
  </div>
  <nav class="abs nav"><span>PRODUCTS</span><span>FAQ</span><span>ABOUT US</span><span>SHIPPING</span><span>INSTALLATION</span><span>BLOG POSTS</span></nav>
  <div class="abs nav-btn nav-search"><svg width="18" height="18" viewBox="0 0 18 18"><circle cx="7.5" cy="7.5" r="5.5" fill="none" stroke="#fff" stroke-width="2"/><line x1="11.5" y1="11.5" x2="16" y2="16" stroke="#fff" stroke-width="2"/></svg></div>
  <div class="abs nav-btn nav-cart"><svg width="20" height="18" viewBox="0 0 20 18"><path d="M1 2h3l2.5 10h10L19 5H5.5" fill="none" stroke="#1d5db5" stroke-width="2"/><circle cx="8" cy="15.5" r="1.6" fill="#1d5db5"/><circle cx="15" cy="15.5" r="1.6" fill="#1d5db5"/></svg></div>
  <h1 class="abs hero-title">SMART LIVING MADE SIMPLE</h1>
  <div class="abs hero-btn">GET MORE INFO</div>
  <div class="abs hero-photo" role="img" aria-label="Tablet showing a home control app"></div>
</header>

<section>
  <h2 class="abs section-title" style="top:712px">WELCOME TO OUR CLEVER DWELLING</h2>
  <p class="abs welcome-text">Control your lights, fans, blinds and appliances from anywhere with one simple app. Our smart switches fit your existing wiring, so you can upgrade your home room by room and set the perfect scene for any occasion with a single tap.</p>
  <div class="abs video" role="img" aria-label="Promotional video still of a hand using a smartphone near a wall switch"></div>
  <svg class="abs play" width="56" height="56" viewBox="0 0 56 56"><circle cx="28" cy="28" r="27" fill="#111"/><path d="M22 17l17 11-17 11z" fill="#fff"/></svg>
</section>

<section>
  <div class="abs collections"></div>
  <h2 class="abs section-title" style="top:1352px">COLLECTIONS AND PRODUCTS</h2>

  <div class="abs tile" style="left:110px;top:1472px;width:572px;height:483px"><div class="tile-fill" role="img" aria-label="White light switch" style="width:320px;height:320px;background:linear-gradient(145deg,#fafafa,#d9d9d9)"></div></div>
  <div class="abs label" style="left:110px;top:1985px;width:572px">Light Switches</div>

  <div class="abs tile" style="left:715px;top:1472px;width:372px;height:198px"><div class="tile-fill" role="img" aria-label="White double wall plug" style="width:200px;height:130px;background:linear-gradient(145deg,#f7f5ee,#cfcbc0)"></div></div>
  <div class="abs label" style="left:715px;top:1697px;width:372px">Wall Plugs</div>

  <div class="abs tile" style="left:715px;top:1757px;width:372px;height:198px"><div class="tile-fill" role="img" aria-label="White fan switch" style="width:150px;height:160px;background:linear-gradient(145deg,#f5f5f5,#bdbdbd)"></div></div>
  <div class="abs label" style="left:715px;top:1985px;width:372px">Fan Switch</div>

  <div class="abs tile" style="left:110px;top:2108px;width:373px;height:197px"><div class="tile-fill" role="img" aria-label="Slide light dimmer" style="width:80px;height:160px;background:linear-gradient(145deg,#f3ede0,#b9ad98)"></div></div>
  <div class="abs label" style="left:110px;top:2332px;width:373px">Light Dimmers</div>

  <div class="abs tile" style="left:110px;top:2393px;width:373px;height:197px"><div class="tile-fill" role="img" aria-label="Black blind controller hub" style="width:180px;height:70px;background:linear-gradient(180deg,#3a3a3a,#0f0f0f)"></div></div>
  <div class="abs label" style="left:110px;top:2620px;width:373px">Blind Controllers</div>

  <div class="abs tile" style="left:516px;top:2108px;width:571px;height:482px"><div class="tile-fill" role="img" aria-label="Brass lantern pendant light" style="width:150px;height:440px;background:linear-gradient(180deg,#3a2a18 0%,#6e4a1e 45%,#e0a533 70%,#5a3c18 100%)"></div></div>
  <div class="abs label" style="left:516px;top:2620px;width:571px">Pendants etc special lighting types</div>
</section>

<section>
  <div class="abs newsletter"></div>
  <h2 class="abs news-title">SUBSCRIBE TO OUR NEWSLETTER</h2>
  <p class="abs news-sub">Sign up to stay in the loop. Receive updates, access to exclusive deals, and more</p>
  <div class="abs news-input">Email Address</div>
  <div class="abs news-btn">SUBSCRIBE</div>
</section>

<section>
  <h2 class="abs feature-title" style="left:112px;top:3335px">WHAT WE DO</h2>
  <p class="abs feature-text" style="left:112px;top:3410px">We supply wireless smart switches that pair with our phone app over WiFi. Turn lights, fans, cameras and appliances on or off from anywhere, at any time, and never wonder again whether something was left running at home.</p>
  <div class="abs pill" style="left:112px;top:3590px">READ MORE</div>
  <div class="abs" role="img" aria-label="Hands holding a smartphone with a smart home app in front of a laptop" style="left:600px;top:3225px;width:488px;height:447px;background:linear-gradient(135deg,#0b2a55,#1c4f8f 50%,#8fa7bf)"></div>

  <div class="abs" role="img" aria-label="Hands holding a tablet with a home control app" style="left:112px;top:3800px;width:488px;height:360px;background:linear-gradient(135deg,#d8d8d8,#8a8f96 55%,#3f4a57)"></div>
  <h2 class="abs feature-title" style="left:672px;top:3820px">HOW WE DO</h2>
  <p class="abs feature-text" style="left:672px;top:3895px">Our switches retrofit your existing wall plates, so no rewiring is needed. Group devices into scenes inside the app and run them with one button. The same device can join several scenes, giving you the right mood for every evening.</p>
  <div class="abs pill" style="left:672px;top:4075px">READ MORE</div>
</section>

<footer>
  <div class="abs footer"></div>
  <h3 class="abs foot-head" style="left:100px">INFORMATION</h3>
  <ul class="abs foot-list" style="left:100px"><li>About Us</li><li>Careers</li><li>Privacy &amp; Security</li><li>Site Map</li><li>Terms of Use</li><li>Blog</li></ul>
  <h3 class="abs foot-head" style="left:290px">HELP &amp; SUPPORT</h3>
  <ul class="abs foot-list" style="left:290px"><li>Recommended Reading</li><li>Submit your Story</li><li>Contact Us</li><li>FAQ</li><li>How to Order</li></ul>
  <h3 class="abs foot-head" style="left:528px">STAY CONNECTED</h3>
  <ul class="abs social"><li><i></i>Friendwall</li><li><i></i>Snapframe</li><li><i></i>Email</li><li><i></i>Workcircle</li></ul>
  <h3 class="abs foot-head" style="left:767px">ABOUT</h3>
  <p class="abs foot-about">We help families bring simple, reliable automation into every room, with friendly support, clear guides and products built to last for many years of calm evenings at home.</p>
  <div class="abs foot-rule"></div>
  <p class="abs copyright">Copyrights © 2018, Our Clever Dwelling. All Rights Reserved.</p>
  <div class="abs cards"><i></i><i></i><i></i><i></i><i></i></div>
</footer>

</body>
</html>
```